"Vine Hollow Excursions" is a top notch Santa Barbara County Wine Tour company.

We provide scenic, boutique and custom wine tours. I need the card to be clean and classy. I will provide our logo. I would like the logo to cover the back side of the card as an option and would like to see a couple color options other then our signature green and gold. I would like to see some creative options and let the designers come up with options.
I need cards for myself and my team. The final design should communicate "A genuine and intimate vineyard journey, sip by sip"
Please use my website for reference www.vinehollowexcursions.example

Target Market(s)

We have a wide range of clients from millennials to baby boomers

Industry/Entity Type

Tour

Contact Information for Business Card

Contact info:
Dale Morton
805-219-6384
info@vinehollowexcursions.example
vinehollowexcursions.example

Colors

Designer to choose colors to be used in the design.

Requirements
Must have
• my logo
Nice to have
• *I would like to have the backside side with the logo and the company statement
• "A genuine and intimate vineyard journey, sip by sip" as an option.
• *I would also like to see what the designers can create!
• *I would like to see an option that incorporates or social: instagram, yelp, trip advisor
Should not have
• I do not want it too busy.

```html
<!DOCTYPE html>
<html lang="en">
<head>
<meta charset="utf-8">
<title>Vine Hollow Excursions – Business Card</title>
<link rel="stylesheet" href="https://fonts.googleapis.com/css2?family=Cinzel:wght@400;600;700&family=Mulish:wght@400;700&display=swap">
<style>
  :root {
    --page-bg: #e9e9e7;
    --card-white: #ffffff;
    --vine-green: #1e6b43;
    --vine-green-deep: #0b4a2c;
    --vine-green-dark: #083b23;
    --gold: #a88466;
    --gold-light: #dcb79a;
    --ink: #3e3e3e;
  }
  * { box-sizing: border-box; margin: 0; padding: 0; }
  html, body {
    width: 1200px; height: 1008px; overflow: hidden;
    background: var(--page-bg);
  }
  .card {
    position: absolute;
    overflow: hidden;
  }
  /* ---------- Front ---------- */
  .card-front {
    left: 318px; top: 166px; width: 558px; height: 319px;
    background: var(--card-white);
  }
  .brand-lockup {
    position: absolute; left: 22px; top: 116px; width: 226px;
    text-align: center;
    font-family: "Cinzel", serif; font-weight: 600;
    color: var(--gold);
  }
  .brand-lockup .brand-main { font-size: 26px; letter-spacing: 1px; line-height: 1; display: block; }
  .brand-lockup .brand-sub { font-size: 14px; letter-spacing: 5px; line-height: 1; display: block; margin-top: 7px; }
  .divider {
    position: absolute; left: 262px; top: 78px; width: 1px; height: 164px;
    background: #c9c9c9;
  }
  .contact {
    position: absolute; left: 276px; top: 84px;
    font-family: "Mulish", sans-serif; color: var(--ink);
    font-size: 14px; line-height: 1;
  }
  .contact .person-name {
    font-family: "Cinzel", serif; font-weight: 700; color: var(--vine-green);
    font-size: 17px; letter-spacing: 0.5px;
  }
  .contact .person-title { margin-top: 6px; }
  .contact .address { margin-top: 14px; line-height: 19px; }
  .contact .lines { margin-top: 6px; }
  .contact .line { display: flex; align-items: center; height: 20.5px; white-space: nowrap; }
  .contact .line svg { width: 13px; height: 13px; margin-right: 6px; flex: none; }
  .contact .web strong { color: var(--vine-green); font-weight: 700; }
  .accent-band { position: absolute; left: 0; bottom: 0; width: 558px; height: 14px; }

  /* ---------- Back ---------- */
  .card-back {
    left: 314px; top: 527px; width: 562px; height: 321px;
    background: radial-gradient(ellipse at 60% 25%, var(--vine-green) 0%, var(--vine-green-deep) 75%);
  }
  .back-scenery {
    position: absolute; left: 0; top: 150px; width: 562px; height: 171px;
    background: linear-gradient(180deg, rgba(30,107,67,0) 0%, rgba(40,120,75,0.45) 55%, rgba(30,107,67,0.35) 100%);
  }
  .back-band {
    position: absolute; left: 0; top: 261px; width: 562px; height: 60px;
    background: rgba(8,59,35,0.35);
  }
  .back-lockup {
    position: absolute; left: 0; top: 128px; width: 562px; text-align: center;
    font-family: "Cinzel", serif; font-weight: 600; color: #ffffff;
  }
  .back-lockup .brand-main { font-size: 36px; letter-spacing: 1.5px; line-height: 1; display: block; }
  .back-lockup .brand-sub { font-size: 19px; letter-spacing: 7px; line-height: 1; display: block; margin-top: 8px; }
  .social-row {
    position: absolute; left: 0; top: 234px; width: 562px;
    display: flex; justify-content: center; gap: 9px;
  }
  .social-row span { width: 14px; height: 14px; border-radius: 50%; background: #ffffff; display: block; }
  .tagline {
    position: absolute; left: 0; top: 268px; width: 562px; text-align: center;
    font-family: "Cinzel", serif; font-weight: 400; color: #ffffff;
    font-size: 13.5px; letter-spacing: 0.6px; white-space: nowrap;
  }
</style>
</head>
<body>

<section class="card card-front" aria-label="Business card front">
  <div class="brand-lockup">
    <span class="brand-main">Vine Hollow</span>
    <span class="brand-sub">Excursions</span>
  </div>

  <div class="divider"></div>

  <div class="contact">
    <div class="person-name">DALE MORTON</div>
    <div class="person-title">Your Title</div>
    <div class="address">Your Address Goes Here<br>Address Line 2</div>
    <div class="lines">
      <div class="line">
        <svg viewBox="0 0 14 14"><circle cx="7" cy="7" r="7" fill="var(--vine-green)"/><rect x="3.5" y="4.5" width="7" height="5" fill="none" stroke="#fff" stroke-width="1"/><path d="M3.5 4.5 L7 7.5 L10.5 4.5" fill="none" stroke="#fff" stroke-width="1"/></svg>
        info@vinehollowexcursions.example
      </div>
      <div class="line">
        <svg viewBox="0 0 14 14"><circle cx="7" cy="7" r="7" fill="var(--vine-green)"/><path d="M3.5 6 Q7 3 10.5 6 L9.5 7 L8.5 6 L5.5 6 L4.5 7 Z M4.5 8 H9.5 V10 H4.5 Z" fill="#fff"/></svg>
        805-219-6384
      </div>
      <div class="line web">
        <svg viewBox="0 0 14 14"><circle cx="7" cy="7" r="7" fill="var(--vine-green)"/><circle cx="7" cy="7" r="3.6" fill="none" stroke="#fff" stroke-width="0.9"/><path d="M3.4 7 H10.6 M7 3.4 V10.6" stroke="#fff" stroke-width="0.9"/></svg>
        <span><strong>vinehollowexcursions</strong>.example</span>
      </div>
    </div>
  </div>

  <svg class="accent-band" viewBox="0 0 558 14" preserveAspectRatio="none">
    <defs>
      <linearGradient id="goldBand" x1="0" x2="1" y1="0" y2="0">
        <stop offset="0" stop-color="#8e6c55"/>
        <stop offset="0.55" stop-color="var(--gold-light)"/>
        <stop offset="1" stop-color="#9a7a62"/>
      </linearGradient>
    </defs>
    <polygon points="0,0 283,0 276,14 0,14" fill="var(--vine-green)"/>
    <polygon points="287,0 558,0 558,14 280,14" fill="url(#goldBand)"/>
  </svg>
</section>

<section class="card card-back" aria-label="Business card back">
  <div class="back-scenery" role="img" aria-label="Faint vineyard rows and hills with a rising sun"></div>
  <div class="back-band"></div>
  <div class="back-lockup">
    <span class="brand-main">Vine Hollow</span>
    <span class="brand-sub">Excursions</span>
  </div>
  <div class="social-row" aria-label="Social profiles">
    <span></span><span></span><span></span>
  </div>
  <p class="tagline">A GENUINE AND INTIMATE VINEYARD JOURNEY, SIP BY SIP</p>
</section>

</body>
</html>
```